Business card design needed

I run a Beautician studio (for 7 years now)
I offer
- Velmo Body Sugaring
- Ruby Glaze
- Nails
- Facials
- Manicure
- Foot Treatment
It might not be necessary to list all those treatments?
Maybe the link to the Website is sufficient?
I leave that up to you ...
(more info on www.FernAndDewByLenka.com.au)
Velmo BodySugaring is our biggest success, It replaces waxing.
I would like to incorporate the logo into the Business Card.
We had many complaints regarding our old Business Cards as the Phone Number was to small.
On the backside, we would like a "your next Appointment" section.
Looking forward to you Design, cheers ... Lenka
Industry/Entity Type
Business
Contact Information for Business Card
Fern by Dew by Lenka
14 Korrin Sqr 3942 Berwick
www.FernAndDewByLenka.com.au
03 9481 2267

```html
<!DOCTYPE html>
<html lang="en">
<head>
<meta charset="utf-8">
<title>Velmo Body Sugaring – Business &amp; Appointment Cards</title>
<link href="https://fonts.googleapis.com/css2?family=Crimson+Pro:wght@600&family=Open+Sans:wght@400;600;700&family=Source+Sans+3:wght@400;600&display=swap" rel="stylesheet">
<style>
  :root {
    --board: #1b1b1b;
    --card: #ffffff;
    --ink: #2b2b2b;
    --ink-soft: #4a4a4a;
    --grey: #666666;
    --rule: #8a8a8a;
    --green: #1f9a3c;
    --orange: #e8551f;
    --amber: #f08a1c;
    --yellow: #f7c51e;
  }
  * { box-sizing: border-box; margin: 0; padding: 0; }
  html, body { width: 1200px; height: 728px; overflow: hidden; background: var(--board); }
  .board { position: relative; width: 1200px; height: 728px; background: var(--board); }
  .card {
    position: absolute; width: 541px; height: 308px; background: var(--card);
    font-family: "Source Sans 3", "Open Sans", sans-serif; color: var(--ink);
    overflow: hidden;
  }
  .card--front  { left: 41px;  top: 37px; }
  .card--appt   { left: 615px; top: 37px; }
  .card--hours  { left: 43px;  top: 380px; }
  .card--appt-alt { left: 624px; top: 384px; }

  /* brand name (logo stand-in) */
  .brand {
    position: absolute; display: flex; align-items: center; gap: 10px;
    font-family: "Open Sans", sans-serif; font-weight: 600; color: var(--ink);
    text-transform: uppercase; letter-spacing: 2px; line-height: 1.25;
  }
  .brand__dot { flex: none; border-radius: 50%; background: var(--amber); }
  .card--front .brand { left: 100px; top: 112px; width: 170px; font-size: 17px; }
  .card--front .brand__dot { width: 26px; height: 26px; }

  .card--front .divider {
    position: absolute; left: 281px; top: 84px; width: 1px; height: 93px; background: var(--rule);
  }
  .contact { position: absolute; left: 296px; top: 86px; }
  .contact__name { font-size: 17px; font-weight: 600; color: var(--ink); }
  .contact__address { font-size: 15px; margin-top: 3px; color: var(--ink-soft); }
  .contact__phone {
    display: flex; align-items: center; gap: 6px; margin-top: 10px;
    font-family: "Open Sans", sans-serif; font-size: 18px; color: var(--ink);
  }
  .contact__phone svg { width: 15px; height: 15px; }

  .footer-band {
    position: absolute; left: 0; right: 0; bottom: 0; height: 34px;
    border-top: 2px solid var(--green);
  }
  .footer-band__fill {
    position: absolute; left: 0; right: 0; bottom: 0; height: 30px;
    background: linear-gradient(90deg, var(--orange), var(--amber) 55%, var(--yellow));
    display: flex; align-items: center; justify-content: center;
    color: #fff; font-family: "Open Sans", sans-serif; font-size: 14px; letter-spacing: 2.2px;
  }

  /* appointment cards */
  .appt__title {
    position: absolute; left: 36px; top: 52px;
    font-family: "Crimson Pro", serif; font-weight: 600; font-size: 20px;
    color: var(--green); letter-spacing: 0.5px;
  }
  .card--appt .brand {
    left: 360px; top: 34px; width: 160px; font-size: 12px; flex-direction: column; gap: 6px; text-align: center;
  }
  .card--appt .brand__dot { width: 30px; height: 30px; }
  .field-row {
    position: absolute; left: 36px; display: flex; align-items: center;
    font-size: 15px; color: var(--ink-soft); white-space: nowrap;
  }
  .field-line { display: inline-block; border-bottom: 1px solid var(--rule); height: 1px; margin: 0 6px; align-self: center; }
  .field-line--dotted { border-bottom-style: dotted; }
  .field-box { display: inline-block; width: 98px; height: 20px; border: 1px solid var(--rule); }
  .row-name { top: 93px; }
  .row-date { top: 130px; }
  .row-next { top: 169px; }
  .row-days {
    position: absolute; left: 33px; top: 207px; display: flex; align-items: center; gap: 6px;
    font-family: "Open Sans", sans-serif; font-weight: 600; font-size: 15px; color: var(--grey);
  }
  .row-days .field-box { width: 34px; margin-right: 6px; }
  .appt__note {
    position: absolute; left: 32px; top: 256px; width: 480px;
    font-size: 13.5px; line-height: 1.35; color: var(--ink-soft);
  }
  .brand-faint {
    position: absolute; left: 100px; top: 120px; width: 380px; text-align: center;
    font-family: "Open Sans", sans-serif; font-weight: 600; font-size: 44px; letter-spacing: 6px;
    color: rgba(120, 120, 120, 0.08); text-transform: uppercase; line-height: 1.1;
  }

  /* hours card */
  .card--hours .brand {
    left: 0; right: 0; top: 40px; justify-content: center; flex-direction: column; gap: 14px;
    font-size: 26px; letter-spacing: 5px; text-align: center;
  }
  .card--hours .brand__dot { width: 70px; height: 70px; }
  .hours__url {
    position: absolute; left: 0; right: 0; top: 206px; text-align: center;
    font-family: "Open Sans", sans-serif; font-size: 15px; letter-spacing: 2px; color: var(--ink);
  }
  .hours__title {
    position: absolute; left: 0; right: 0; top: 238px; text-align: center;
    font-family: "Open Sans", sans-serif; font-weight: 700; font-size: 20px; letter-spacing: 1.5px; color: var(--grey);
  }
  .hours__times {
    position: absolute; left: 0; right: 0; top: 274px; text-align: center;
    font-family: "Open Sans", sans-serif; font-weight: 600; font-size: 15px; color: var(--grey);
  }
  .hours__sep { color: #aaa; margin: 0 8px; font-weight: 400; }
</style>
</head>
<body>
<main class="board">

  <!-- Business card: front -->
  <section class="card card--front">
    <div class="brand"><span class="brand__dot"></span><span>Velmo Body Sugaring</span></div>
    <div class="divider"></div>
    <div class="contact">
      <p class="contact__name">Fern by Dew by Lenka</p>
      <p class="contact__address">14 Korrin Sqr 3942 Berwick</p>
      <p class="contact__phone">
        <svg viewBox="0 0 16 16" aria-hidden="true"><circle cx="8" cy="8" r="7.2" fill="none" stroke="#1f9a3c" stroke-width="1.3"/><path d="M5.3 4.2l1.4 1.9-.8 1c.5 1 1.2 1.8 2.2 2.3l1-.8 1.9 1.4-.7 1.3c-2.9-.4-5.1-2.6-5.6-5.5z" fill="#1f9a3c"/></svg>
        03 9481 2267
      </p>
    </div>
    <div class="footer-band"><div class="footer-band__fill">www.FernAndDewByLenka.com.au</div></div>
  </section>

  <!-- Appointment card -->
  <section class="card card--appt">
    <h2 class="appt__title">YOUR APPOINTMENT</h2>
    <div class="brand"><span class="brand__dot"></span><span>Velmo Body Sugaring</span></div>
    <div class="field-row row-name">Name :<span class="field-line field-line--dotted" style="width:290px"></span></div>
    <div class="field-row row-date">Date :<span class="field-line" style="width:95px;margin-left:18px"></span>Time :<span class="field-line" style="width:90px"></span>am / pm</div>
    <div class="field-row row-next">Next Appointment<span class="field-box" style="margin-left:10px"></span><span class="field-box" style="margin-left:32px"></span></div>
    <div class="row-days">MON <span class="field-box"></span>TUE <span class="field-box"></span>WED <span class="field-box"></span>THU <span class="field-box"></span>FRI <span class="field-box"></span>SAT <span class="field-box"></span></div>
    <p class="appt__note">It would be appreciated if 24 hours notice could be given if you are unable to attend an appointment</p>
  </section>

  <!-- Business card: back with hours -->
  <section class="card card--hours">
    <div class="brand"><span class="brand__dot"></span><span>Velmo Body Sugaring</span></div>
    <p class="hours__url">www.FernAndDewByLenka.com.au</p>
    <h2 class="hours__title">Hours of Operation</h2>
    <p class="hours__times">Mon - Fri: 7.30am - 7.00pm<span class="hours__sep">|</span>Saturday: 7.30am - 12.00pm</p>
  </section>

  <!-- Appointment card: alternate -->
  <section class="card card--appt-alt">
    <div class="brand-faint" aria-hidden="true">Velmo Body Sugaring</div>
    <h2 class="appt__title">YOUR APPOINTMENT</h2>
    <div class="field-row row-name">Name :<span class="field-line field-line--dotted" style="width:290px"></span></div>
    <div class="field-row row-date">Date :<span class="field-line" style="width:95px;margin-left:18px"></span>Time :<span class="field-line" style="width:90px"></span>am / pm</div>
    <div class="field-row row-next">Next Appointment<span class="field-box" style="margin-left:10px"></span><span class="field-box" style="margin-left:32px"></span></div>
    <div class="row-days">MON <span class="field-box"></span>TUE <span class="field-box"></span>WED <span class="field-box"></span>THU <span class="field-box"></span>FRI <span class="field-box"></span>SAT <span class="field-box"></span></div>
    <p class="appt__note">It would be appreciated if 24 hours notice could be given if you are unable to attend an appointment</p>
  </section>

</main>
</body>
</html>
```